Redesign of business card for Cedar Ridge Mechanical

We are looking for a new design for our business cards for Cedar Ridge Mechanical. We are a plumbing & HVAC construction company, operating on the West Coast of Canada and USA. Logo attached.
Industry/Entity Type
Construction - Plumbing & HVAC
Contact Information for Business Card
Name, address, phone numbers, email, website address
Look and feel
Each slider illustrates characteristics of the customer's brand and the style your logo design should communicate.

```html
<!DOCTYPE html>
<html lang="en">
<head>
<meta charset="UTF-8">
<title>Cedar Ridge Mechanical – Business Card</title>
<link rel="stylesheet" href="https://fonts.googleapis.com/css2?family=Poppins:wght@300;400;600&display=swap">
<style>
  :root {
    --stage: #232323;
    --paper: #e6e7e6;
    --ink: #111111;
    --ink-soft: #2a2a2a;
    --emboss: #d3d4d3;
    --emboss-light: #f2f3f2;
  }
  * { margin: 0; padding: 0; box-sizing: border-box; }
  html, body {
    width: 1200px; height: 780px; overflow: hidden;
    background: var(--stage);
    font-family: "Poppins", sans-serif;
  }
  .stage {
    position: relative; width: 1200px; height: 780px;
    display: flex; align-items: center; justify-content: center; gap: 40px;
  }
  .card {
    position: relative; width: 540px; height: 310px;
    background: var(--paper);
    box-shadow: 0 14px 30px rgba(0,0,0,.45);
  }
  /* Front */
  .brand {
    position: absolute; top: 30px; right: 32px;
    display: flex; align-items: center; gap: 10px;
    color: var(--ink); font-weight: 600; font-size: 15px;
    letter-spacing: .06em; text-transform: uppercase;
  }
  .brand-mark { width: 14px; height: 14px; background: var(--ink); }
  .contact {
    position: absolute; top: 86px; right: 32px;
    text-align: right; color: var(--ink-soft);
    font-weight: 400; font-size: 13px; line-height: 1.45;
  }
  .contact .address { margin-bottom: 10px; }
  .contact-line { display: flex; align-items: center; justify-content: flex-end; gap: 10px; }
  .contact-line svg { width: 12px; height: 12px; flex: none; }
  .person { position: absolute; left: 32px; bottom: 30px; color: var(--ink); }
  .person-name { font-size: 26px; line-height: 1.1; font-weight: 300; }
  .person-name strong { font-weight: 600; }
  .person-title { font-size: 13px; font-weight: 400; margin-top: 4px; }
  /* Back */
  .card-back { display: flex; align-items: center; justify-content: center; }
  .brand-emboss {
    display: flex; align-items: center; gap: 14px;
    color: var(--emboss); font-weight: 600; font-size: 26px;
    letter-spacing: .06em; text-transform: uppercase;
  }
  .brand-emboss .brand-mark { width: 24px; height: 24px; background: var(--emboss); }
</style>
</head>
<body>
<main class="stage">
  <section class="card card-front">
    <div class="brand"><span>Cedar Ridge Mechanical</span><span class="brand-mark"></span></div>
    <div class="contact">
      <p class="address">418 Harbor Lane Suite 120<br>Bellingham, WA 98225</p>
      <p class="contact-line">(360) 555-0147
        <svg viewBox="0 0 12 12" aria-hidden="true"><circle cx="6" cy="6" r="6" fill="#111"/><path d="M4 3.2l1 1.3-.6.8a4 4 0 0 0 2.3 2.3l.8-.6 1.3 1-.6 1A5 5 0 0 1 3 4l1-.8z" fill="#e6e7e6"/></svg>
      </p>
      <p class="contact-line">info@cedarridgemech.com
        <svg viewBox="0 0 12 12" aria-hidden="true"><circle cx="6" cy="6" r="6" fill="#111"/><rect x="2.8" y="3.8" width="6.4" height="4.4" fill="none" stroke="#e6e7e6" stroke-width=".9"/><path d="M2.8 3.8L6 6.3l3.2-2.5" fill="none" stroke="#e6e7e6" stroke-width=".9"/></svg>
      </p>
      <p class="contact-line">www.cedarridgemech.com
        <svg viewBox="0 0 12 12" aria-hidden="true"><circle cx="6" cy="6" r="5.5" fill="none" stroke="#111" stroke-width="1"/><ellipse cx="6" cy="6" rx="2.3" ry="5.5" fill="none" stroke="#111" stroke-width=".8"/><path d="M.5 6h11" stroke="#111" stroke-width=".8"/></svg>
      </p>
    </div>
    <div class="person">
      <p class="person-name"><strong>Marta</strong> Novak</p>
      <p class="person-title">Founder &amp; CEO</p>
    </div>
  </section>
  <section class="card card-back">
    <div class="brand-emboss"><span class="brand-mark"></span><span>Cedar Ridge Mechanical</span></div>
  </section>
</main>
</body>
</html>
```